Whitcombe Business Card Design

The name of the business is Dario Whitcombe, CPA LLC
The service that we offer is Accounting, Tax & Consulting Services. I need it to have the following items:
Dario Whitcombe, Principal
Phone Number
Email Address
Physical Address

I have attached the company logo, one in black and one in white. Please provide a design in black background and the other in white background. Please include "Accounting, Tax & Consulting Services". I want the business card to be clean and very professional.

```html
<!DOCTYPE html>
<html lang="en">
<head>
<meta charset="utf-8">
<title>Dario Whitcombe, CPA LLC — Business Cards</title>
<link rel="stylesheet" href="https://fonts.googleapis.com/css2?family=Montserrat:wght@400;500;600;700&display=swap">
<style>
  :root {
    --backdrop: #2b2b2b;
    --card-black: #0b0b0b;
    --card-white: #ffffff;
    --brand-red: #9b1a1d;
    --ink-dark: #3a3a3c;
    --ink-grey: #8a8a8a;
    --ink-white: #ffffff;
  }
  * { box-sizing: border-box; margin: 0; padding: 0; }
  html, body {
    width: 1200px; height: 1024px; overflow: hidden;
    background: var(--backdrop);
    font-family: "Montserrat", sans-serif;
  }
  .canvas {
    width: 1200px; height: 1024px;
    display: flex; flex-direction: column; align-items: center; justify-content: center;
    gap: 64px;
  }
  .card {
    position: relative;
    width: 700px; height: 400px;
    overflow: hidden;
    box-shadow: 0 12px 30px rgba(0,0,0,0.45);
  }

  /* Front: black */
  .card--front { background: var(--card-black); }
  .front-brand {
    position: absolute; left: 150px; top: 188px;
    color: var(--ink-white);
  }
  .brand-name {
    font-weight: 600; font-size: 24px; letter-spacing: 0.5px;
    text-transform: uppercase; line-height: 1; white-space: nowrap;
  }
  .brand-sub {
    margin-top: 6px;
    font-weight: 500; font-size: 12.5px; letter-spacing: 2.2px;
    text-transform: uppercase; white-space: nowrap;
  }
  .services-band {
    position: absolute; left: 0; right: 0; top: 268px; height: 34px;
    background: var(--brand-red);
    display: flex; align-items: center; padding-left: 150px;
    color: var(--ink-white);
    font-weight: 500; font-size: 14px; letter-spacing: 1.6px;
    text-transform: uppercase;
  }

  /* Back: white */
  .card--back { background: var(--card-white); }
  .person {
    position: absolute; right: 48px; top: 40px; text-align: right;
  }
  .person-name {
    color: var(--brand-red);
    font-weight: 700; font-size: 26px; letter-spacing: 0.5px;
    text-transform: uppercase; line-height: 1.1;
  }
  .person-title {
    color: var(--ink-grey); font-weight: 400; font-size: 16px; margin-top: 2px;
  }
  .back-brand {
    position: absolute; left: 48px; top: 150px;
    display: grid; grid-template-columns: 14px auto; column-gap: 12px; row-gap: 6px;
    align-items: center;
  }
  .brand-square {
    width: 14px; height: 14px; background: var(--brand-red);
  }
  .back-brand .brand-name { color: var(--ink-dark); font-size: 20px; }
  .back-brand .brand-sub {
    grid-column: 2; margin-top: 0;
    color: var(--ink-grey); font-size: 10.5px; letter-spacing: 2px;
  }
  .contact-list {
    position: absolute; left: 48px; bottom: 52px;
    list-style: none;
    color: var(--ink-grey); font-size: 15px; font-weight: 400; line-height: 1.5;
  }
  .contact-list li { display: flex; align-items: flex-start; gap: 10px; }
  .contact-icon { flex: none; width: 16px; height: 16px; margin-top: 4px; }
  .contact-list .no-icon { padding-left: 26px; }
</style>
</head>
<body>
<main class="canvas">

  <section class="card card--front" aria-label="Business card front">
    <div class="front-brand">
      <p class="brand-name">Dario Whitcombe, CPA LLC</p>
      <p class="brand-sub">Certified Public Accountant</p>
    </div>
    <div class="services-band">Accounting, Tax &amp; Consulting Services</div>
  </section>

  <section class="card card--back" aria-label="Business card back">
    <div class="person">
      <p class="person-name">Dario Whitcombe</p>
      <p class="person-title">Principal</p>
    </div>

    <div class="back-brand">
      <span class="brand-square"></span>
      <p class="brand-name">Dario Whitcombe, CPA LLC</p>
      <p class="brand-sub">Certified Public Accountant</p>
    </div>

    <ul class="contact-list">
      <li>
        <svg class="contact-icon" viewBox="0 0 16 16" aria-hidden="true">
          <circle cx="8" cy="8" r="8" fill="var(--brand-red)"/>
          <path d="M5.2 4.3l1.3-.3.8 1.8-.9.7a5 5 0 0 0 2.3 2.3l.7-.9 1.8.8-.3 1.3c-3.2.4-6-2.4-5.7-5.7z" fill="#fff"/>
        </svg>
        <span>(555) 214-0198</span>
      </li>
      <li>
        <svg class="contact-icon" viewBox="0 0 16 16" aria-hidden="true">
          <circle cx="8" cy="8" r="8" fill="var(--brand-red)"/>
          <rect x="4" y="5" width="8" height="6" fill="none" stroke="#fff" stroke-width="1.1"/>
          <path d="M4 5l4 3.2L12 5" fill="none" stroke="#fff" stroke-width="1.1"/>
        </svg>
        <span>info@dariowhitcombe.com</span>
      </li>
      <li class="no-icon"><span>123, Your Street Name, your<br>city, lane 00125</span></li>
    </ul>
  </section>

</main>
</body>
</html>
```